velorimo.gr wordpress makeover

We need a makeover of our wordpress website velorimo.gr We are a company that provides astrology services via phone either by billable phone number or by prepaid packages.This is what we sell. Moreover, we share everyday astrology related articles to our blog. It will be a multy page website. Our goal is always to sell our phone prepaid packages or to make the visitor of the website call our billable numbers. Our website should have:
-a home page introducing its content (astrologers, call packages, blog section with categories).
-astrologers page (you can see the existing one to understand)
-Phone packages page (eshop page where you can buy prepaid phone packages. woo commerce maybe)
- Blog page divined by categories.
The website should have places for display banners eg. a sidebar.
I will provide some screen shots of websites we like. You can always visit our existing website www.velorimo.gr to see it for yourself.

Target Market(s)

people seeking for future telling - astrologer services via phone. People who like to be informed about everyday astrology predictions

Industry/Entity Type

Astrology - tarot services via phone

Coding

Coded - Design and coding required

Number of Pages Required

5+ page

Font styles to use
Decorative
Script

Colors
6B429C
8869AF
B7A5CE
E3DAEB
F3F0F8

Requirements
Must have
• -Home page -Astrologers page -Phone packages page (eshop) -Blog page with categories - Made following the guidelines of quenbly so as to be efficient in quenbly ads marketing. Mobile friendly.
Nice to have
• Nice call to action buttons to call or buy packages. Sidebar with banner ads of maybe our offers.

```html
<!DOCTYPE html>
<html lang="el">
<head>
<meta charset="utf-8">
<title>velorimo.gr</title>
<link rel="stylesheet" href="https://fonts.googleapis.com/css2?family=Roboto:wght@300;400;500;700&display=swap">
<style>
:root{
  --purple:#a3479a;
  --purple-dark:#8a3a88;
  --purple-band:#a24a9c;
  --night:#1a1f5e;
  --night-deep:#0b0f33;
  --ink:#222;
  --muted:#9a9a9a;
  --line:#e2e2e2;
  --white:#fff;
  --footer:#0d0d14;
}
*{box-sizing:border-box;margin:0;padding:0}
html,body{width:1200px;height:3423px;overflow:hidden}
body{font-family:"Roboto",sans-serif;color:var(--ink);background:var(--white);position:relative}
.abs{position:absolute}
.wordmark{display:flex;align-items:center;gap:6px;font-size:42px;font-weight:400;color:#222;letter-spacing:-.5px}
.wordmark .dot{width:26px;height:26px;border-radius:50%;background:#8c8c8c}
/* header */
.site-header{top:0;left:0;width:1200px;height:84px;background:var(--white)}
.site-header .wordmark{position:absolute;left:113px;top:17px}
.main-nav{position:absolute;left:528px;top:33px;display:flex;font-size:16px;color:#333}
.main-nav span{position:absolute;white-space:nowrap}
.search-icon{position:absolute;left:1068px;top:34px}
/* hero */
.hero{top:84px;left:0;width:1200px;height:600px;background:radial-gradient(circle at 380px 260px,#8a7ae0 0,#3b3aa6 25%,var(--night) 55%,var(--night-deep) 100%)}
.hero-art{position:absolute;left:0;top:60px;width:560px;height:540px;background:radial-gradient(circle at 380px 200px,rgba(200,180,255,.55) 0,rgba(140,120,230,.3) 35%,rgba(220,120,170,.25) 70%,transparent 85%)}
.hero-title{position:absolute;left:598px;top:140px;font-size:48px;font-weight:700;color:var(--white);line-height:73px}
.hero-text{position:absolute;left:598px;top:302px;width:430px;font-size:15.5px;line-height:26px;color:#e6e4ff;font-weight:300}
.btn-call{position:absolute;left:598px;top:408px;width:124px;height:41px;border-radius:21px;background:var(--purple);color:var(--white);font-size:16px;font-weight:500;display:flex;align-items:center;justify-content:center;gap:9px}
.hero-dots{position:absolute;left:572px;top:550px;display:flex;gap:6px}
.hero-dots i{width:9px;height:9px;border-radius:50%;background:var(--white)}
.hero-dots i.on{background:#d98bd0}
.hero-thumbs .thumb{position:absolute;left:1100px;width:87px;height:77px;border:2px solid #dcdcff;border-radius:5px;background:radial-gradient(circle,#6d7bd8,#1b2061)}
/* tabs */
.tabs{top:768px;left:0;width:1200px;font-size:26px;color:var(--muted)}
.tabs span{position:absolute;white-space:nowrap}
.tabs .active{color:var(--purple);text-decoration:underline;text-underline-offset:5px}
.section-title{font-size:29px;font-weight:500;color:#222;white-space:nowrap}
/* blog cards */
.post-card{position:absolute;width:310px;height:329px;border:1px solid var(--line);background:var(--white)}
.post-card .thumb-img{height:199px}
.post-meta{display:flex;align-items:center;gap:6px;color:var(--purple);font-size:14px;font-weight:500;margin:19px 0 0 20px}
.post-title{margin:13px 20px 0;font-size:18.5px;line-height:30px;color:#222}
/* sidebar */
.recent-box{left:779px;top:926px;width:309px;height:681px;border:1px solid var(--line)}
.recent-item{position:absolute;left:19px;width:270px;font-size:20px;line-height:30px;color:#333}
.recent-item .post-meta{margin:8px 0 0}
.recent-item hr{border:0;border-top:1px solid var(--line);margin-top:13px}
/* astrologers */
.astrologers{top:1697px;left:0;width:1200px;height:771px;background:radial-gradient(circle at 900px 200px,#b45eae 0,var(--purple-band) 45%,#8e3c8c 100%)}
.astrologers h2{position:absolute;top:76px;width:100%;text-align:center;color:var(--white);font-size:29px;font-weight:500}
.astro-card{position:absolute;top:160px;width:300px;height:439px;background:var(--white)}
.astro-card .portrait{height:216px}
.astro-bar{height:63px;background:var(--purple);border:2px solid var(--white);display:flex;align-items:center;color:var(--white)}
.astro-bar .num{display:flex;align-items:center;gap:8px;padding-left:18px;width:150px;font-size:29px;font-weight:500;border-right:1px solid rgba(255,255,255,.6);height:32px}
.astro-bar .name{flex:1;text-align:center;font-size:19px;line-height:22px}
.astro-desc{padding:15px 18px;font-size:13.2px;line-height:21.5px;text-align:center;color:#444}
.btn-more{position:absolute;left:490px;top:642px;width:220px;height:45px;border:2px solid var(--white);border-radius:23px;color:var(--white);font-size:16px;font-weight:500;display:flex;align-items:center;justify-content:center}
/* packages */
.packages-title{top:2540px;width:1200px;text-align:center}
.package{position:absolute;top:2641px;width:307px;height:340px;text-align:center}
.package.featured{background:var(--purple);color:var(--white)}
.package h3{margin-top:46px;font-size:24px;font-weight:500;color:var(--purple)}
.package.featured h3{color:var(--white)}
.package .price{margin-top:22px;font-size:70px;font-weight:700;line-height:80px;color:#1e1e1e}
.package.featured .price{color:var(--white)}
.package p{margin:22px auto 0;width:270px;font-size:14px;line-height:26px;color:#555;font-weight:300}
.package.featured p{color:#fbe9f8}
/* footer */
.site-footer{top:3070px;left:0;width:1200px;height:353px;background:radial-gradient(circle at 640px 120px,#2a1e2e 0,var(--footer) 60%)}
.site-footer .wordmark{position:absolute;left:0;width:1200px;justify-content:center;top:76px;color:var(--white)}
.site-footer .wordmark .dot{background:#6b3c2a}
.footer-nav{position:absolute;top:160px;width:1200px;display:flex;justify-content:center;gap:52px;color:var(--white);font-size:16px}
.social{position:absolute;top:210px;width:1200px;display:flex;justify-content:center;gap:15px}
.social i{width:32px;height:32px;border-radius:50%;background:var(--purple)}
.copyright{position:absolute;top:266px;width:1200px;text-align:center;color:var(--white);font-size:13.5px}
</style>
</head>
<body>

<header class="site-header abs">
  <div class="wordmark">velorimo<span class="dot"></span></div>
  <nav class="main-nav">
    <span style="left:0">Ιστολόγιο</span>
    <span style="left:122px">Μέντιουμ Αστρολόγοι</span>
    <span style="left:333px">Αγορά Χρόνου Ομιλίας</span>
  </nav>
  <svg class="search-icon" width="17" height="17" viewBox="0 0 17 17"><circle cx="7" cy="7" r="5.3" fill="none" stroke="#a3479a" stroke-width="2.4"/><line x1="11" y1="11" x2="15.5" y2="15.5" stroke="#a3479a" stroke-width="2.6" stroke-linecap="round"/></svg>
</header>

<section class="hero abs">
  <div class="hero-art" role="img" aria-label="Cupped hands holding a glowing zodiac wheel against a starry sky"></div>
  <h1 class="hero-title">Τα ζώδια για σήμερα<br>Πέμπτη 17/11</h1>
  <p class="hero-text">Τα ζώδια για σήμερα 17/11 Κριός θα νιώσετε έντονη την ανάγκη αποσυρθείτε από την κοινωνικοποίηση και μείνετε μέσα</p>
  <div class="btn-call">
    <svg width="14" height="14" viewBox="0 0 24 24"><path fill="#fff" d="M6.6 10.8a15.1 15.1 0 0 0 6.6 6.6l2.2-2.2c.3-.3.7-.4 1-.2 1.1.4 2.3.6 3.6.6.6 0 1 .4 1 1V20c0 .6-.4 1-1 1A17 17 0 0 1 3 4c0-.6.4-1 1-1h3.5c.6 0 1 .4 1 1 0 1.3.2 2.5.6 3.6.1.3 0 .7-.2 1z"/></svg>κλήση
  </div>
  <div class="hero-dots"><i></i><i class="on"></i><i></i><i></i></div>
  <div class="hero-thumbs">
    <div class="thumb" role="img" aria-label="Zodiac wheel slide preview" style="top:155px"></div>
    <div class="thumb" role="img" aria-label="Astrology portal slide preview" style="top:259px;background:radial-gradient(circle,#8891a8,#1b2030)"></div>
    <div class="thumb" role="img" aria-label="Glowing zodiac circle slide preview" style="top:363px;background:radial-gradient(circle,#3fd6f0,#0b3b6b)"></div>
  </div>
</section>

<nav class="tabs abs">
  <span class="active" style="left:113px">αστρολογία</span>
  <span style="left:323px">αστρολογία</span>
  <span style="left:532px">αστρολογία</span>
  <span style="left:740px">αστρολογία</span>
  <span style="left:949px">αστρολογία</span>
</nav>

<h2 class="section-title abs" style="left:112px;top:850px">Τελευταίο ιστολόγιο</h2>
<h2 class="section-title abs" style="left:781px;top:850px">Πρόσφατα Άρθρα</h2>

<article class="post-card" style="left:112px;top:926px">
  <div class="thumb-img" role="img" aria-label="Hands laying out tarot cards beside a candle" style="background:linear-gradient(135deg,#8d8276,#5a4d43 60%,#a08a73)"></div>
  <div class="post-meta"><svg width="13" height="13" viewBox="0 0 14 14"><circle cx="7" cy="7" r="5.8" fill="none" stroke="#a3479a" stroke-width="1.8"/><path d="M7 3.8V7l2.2 1.5" fill="none" stroke="#a3479a" stroke-width="1.6"/></svg>10 ώρες πριν</div>
  <h3 class="post-title">Τα ζώδια για σήμερα Παρασκευή 18/11</h3>
</article>
<article class="post-card" style="left:444px;top:926px">
  <div class="thumb-img" role="img" aria-label="Illustrated fortune teller with tarot cards" style="background:linear-gradient(180deg,#d8c7dd,#c3a2c8 55%,#e8e8e8 56%)"></div>
  <div class="post-meta"><svg width="13" height="13" viewBox="0 0 14 14"><circle cx="7" cy="7" r="5.8" fill="none" stroke="#a3479a" stroke-width="1.8"/><path d="M7 3.8V7l2.2 1.5" fill="none" stroke="#a3479a" stroke-width="1.6"/></svg>15 ώρες πριν</div>
  <h3 class="post-title">Ταρώ για σήμερα Πέμπτη 17/11</h3>
</article>
<article class="post-card" style="left:112px;top:1281px">
  <div class="thumb-img" role="img" aria-label="Candle glowing beside a spread of cards in the dark" style="background:radial-gradient(circle at 50% 40%,#7a3a16,#2a1710 45%,#151515)"></div>
  <div class="post-meta"><svg width="13" height="13" viewBox="0 0 14 14"><circle cx="7" cy="7" r="5.8" fill="none" stroke="#a3479a" stroke-width="1.8"/><path d="M7 3.8V7l2.2 1.5" fill="none" stroke="#a3479a" stroke-width="1.6"/></svg>2 ημέρες πριν</div>
  <h3 class="post-title">Τα ζώδια για σήμερα Τετάρτη 16/11</h3>
</article>
<article class="post-card" style="left:444px;top:1281px">
  <div class="thumb-img" role="img" aria-label="Cartoon magician with a rabbit in a top hat" style="background:linear-gradient(135deg,#cfe6f2,#a9c7e0 50%,#e9f0d0)"></div>
  <div class="post-meta"><svg width="13" height="13" viewBox="0 0 14 14"><circle cx="7" cy="7" r="5.8" fill="none" stroke="#a3479a" stroke-width="1.8"/><path d="M7 3.8V7l2.2 1.5" fill="none" stroke="#a3479a" stroke-width="1.6"/></svg>3 ημέρες πριν</div>
  <h3 class="post-title">Ταρώ για σήμερα Τρίτη 15/11</h3>
</article>

<aside class="recent-box abs">
  <div class="recent-item" style="top:20px">Τα ζώδια για σήμερα Παρασκευή 18/11
    <div class="post-meta"><svg width="13" height="13" viewBox="0 0 14 14"><circle cx="7" cy="7" r="5.8" fill="none" stroke="#a3479a" stroke-width="1.8"/><path d="M7 3.8V7l2.2 1.5" fill="none" stroke="#a3479a" stroke-width="1.6"/></svg>10 ώρες πριν</div><hr></div>
  <div class="recent-item" style="top:151px">Ταρώ για σήμερα Πέμπτη 1 7/11
    <div class="post-meta"><svg width="13" height="13" viewBox="0 0 14 14"><circle cx="7" cy="7" r="5.8" fill="none" stroke="#a3479a" stroke-width="1.8"/><path d="M7 3.8V7l2.2 1.5" fill="none" stroke="#a3479a" stroke-width="1.6"/></svg>15 ώρες πριν</div><hr></div>
  <div class="recent-item" style="top:282px">Τα ζώδια για σήμερα Πέμπτη 17/11
    <div class="post-meta"><svg width="13" height="13" viewBox="0 0 14 14"><circle cx="7" cy="7" r="5.8" fill="none" stroke="#a3479a" stroke-width="1.8"/><path d="M7 3.8V7l2.2 1.5" fill="none" stroke="#a3479a" stroke-width="1.6"/></svg>1 ημέρα πριν</div><hr></div>
  <div class="recent-item" style="top:413px">Ταρώ για σήμερα Τετάρτη 16/11
    <div class="post-meta"><svg width="13" height="13" viewBox="0 0 14 14"><circle cx="7" cy="7" r="5.8" fill="none" stroke="#a3479a" stroke-width="1.8"/><path d="M7 3.8V7l2.2 1.5" fill="none" stroke="#a3479a" stroke-width="1.6"/></svg>2 ημέρες πριν</div><hr></div>
  <div class="recent-item" style="top:553px">Τα ζώδια για σήμερα Πέμπτη 17/11
    <div class="post-meta"><svg width="13" height="13" viewBox="0 0 14 14"><circle cx="7" cy="7" r="5.8" fill="none" stroke="#a3479a" stroke-width="1.8"/><path d="M7 3.8V7l2.2 1.5" fill="none" stroke="#a3479a" stroke-width="1.6"/></svg>1 ημέρα πριν</div></div>
</aside>

<section class="astrologers abs">
  <h2>Οι αστρολόγοι μας</h2>
  <div class="astro-card" style="left:112px">
    <div class="portrait" role="img" aria-label="Astrologer portrait in bright seaside light" style="background:linear-gradient(180deg,#f4ede4,#e9dccb)"></div>
    <div class="astro-bar"><div class="num"><svg width="24" height="24" viewBox="0 0 24 24"><path fill="#fff" d="M6.6 10.8a15.1 15.1 0 0 0 6.6 6.6l2.2-2.2c.3-.3.7-.4 1-.2 1.1.4 2.3.6 3.6.6.6 0 1 .4 1 1V20c0 .6-.4 1-1 1A17 17 0 0 1 3 4c0-.6.4-1 1-1h3.5c.6 0 1 .4 1 1 0 1.3.2 2.5.6 3.6.1.3 0 .7-.2 1z"/></svg>14977</div><div class="name">Λήδα Καρνή</div></div>
    <p class="astro-desc">Δυνατό μέντιουμ. Θα σας βοηθήσω να λύσετε τα ερωτικά και επαγγελματικά σας προβλήματα με σίγουρες απαντήσεις μέσω της επιστήμης της αστρολογίας. Είμαι ο αστρολόγος που ψάχνεις! Μια τηλεφωνική πρόβλεψη θα σας πείσει.</p>
  </div>
  <div class="astro-card" style="left:450px">
    <div class="portrait" role="img" aria-label="Astrologer portrait meditating" style="background:linear-gradient(180deg,#c9d6d6,#b3c4c4)"></div>
    <div class="astro-bar"><div class="num"><svg width="24" height="24" viewBox="0 0 24 24"><path fill="#fff" d="M6.6 10.8a15.1 15.1 0 0 0 6.6 6.6l2.2-2.2c.3-.3.7-.4 1-.2 1.1.4 2.3.6 3.6.6.6 0 1 .4 1 1V20c0 .6-.4 1-1 1A17 17 0 0 1 3 4c0-.6.4-1 1-1h3.5c.6 0 1 .4 1 1 0 1.3.2 2.5.6 3.6.1.3 0 .7-.2 1z"/></svg>14977</div><div class="name">Ελένη<br>Βαρσάμη</div></div>
    <p class="astro-desc">Αστρολόγος με εξειδίκευση στην Αστροψυχολογία, με πολλά χρόνια έρευνας πάνω στις ανθρώπινες σχέσεις. Κάλεσε τώρα για μια προσωπική αστρολογική πρόβλεψη. Έχω τις απαντήσεις στα ερωτήματα που σε απασχολούν.</p>
  </div>
  <div class="astro-card" style="left:789px">
    <div class="portrait" role="img" aria-label="Astrologer portrait outdoors in autumn light" style="background:linear-gradient(135deg,#c9a34c,#6b5a3a 55%,#3e3a2c)"></div>
    <div class="astro-bar"><div class="num"><svg width="24" height="24" viewBox="0 0 24 24"><path fill="#fff" d="M6.6 10.8a15.1 15.1 0 0 0 6.6 6.6l2.2-2.2c.3-.3.7-.4 1-.2 1.1.4 2.3.6 3.6.6.6 0 1 .4 1 1V20c0 .6-.4 1-1 1A17 17 0 0 1 3 4c0-.6.4-1 1-1h3.5c.6 0 1 .4 1 1 0 1.3.2 2.5.6 3.6.1.3 0 .7-.2 1z"/></svg>14977</div><div class="name">Ίλια</div></div>
    <p class="astro-desc">Επικοινώνησε μαζί μου για να διώξεις κάθε αμφιβολία στα θέματα που σε απασχολούν. Η εμπειρία μου θα σου δώσει αυτό που ζητάς με τον πιο έγκυρο τρόπο. Ψάχνεις αστρολογική γραμμή; Η καλύτερη γραμμή τηλεφωνικών προβλέψεων.</p>
  </div>
  <div class="btn-more">Δείτε περισσότερα</div>
</section>

<h2 class="section-title packages-title abs">προσφορές πακέτων</h2>
<div class="package" style="left:112px">
  <h3>30 ομιλία</h3><div class="price">30€</div>
  <p>Πληρωμή με χρεωστική / πιστωτική κάρτα μέσω Kalopay&nbsp; Πληρωμή με κατάθεση στους παρακάτω λογαριασμούς</p>
</div>
<div class="package featured" style="left:445px">
  <h3>60 ομιλία</h3><div class="price">50€</div>
  <p>Πληρωμή με χρεωστική / πιστωτική κάρτα μέσω Kalopay&nbsp; Πληρωμή με κατάθεση στους παρακάτω λογαριασμούς</p>
</div>
<div class="package" style="left:778px">
  <h3>120 ομιλία</h3><div class="price">75€</div>
  <p>Πληρωμή με χρεωστική / πιστωτική κάρτα μέσω Kalopay&nbsp; Πληρωμή με κατάθεση στους παρακάτω λογαριασμούς</p>
</div>

<footer class="site-footer abs">
  <div class="wordmark">velorimo<span class="dot"></span></div>
  <nav class="footer-nav"><span>Ιστολόγιο</span><span>Μέντιουμ Αστρολόγοι</span><span>Αγορά Χρόνου Ομιλίας</span></nav>
  <div class="social"><i></i><i></i><i></i><i></i></div>
  <p class="copyright">© copyrights 2022 velorimo | Όλα τα δικαιώματα διατηρούνται.</p>
</footer>

</body>
</html>
```